Birchline Septic Solutions

Would like to see some single sided ones but would also like to see some double sided with one sided only being the logo. Owners name is Colin Vandro. Phone number is 555-214-0387
Services are pumping, inspections, installs, and repairs

Contact Information for Business Card

555-241-0387 Colin Vandro Maplebrook, OH

```html
<!DOCTYPE html>
<html lang="en">
<head>
<meta charset="utf-8">
<title>Birchline Septic Solutions – Business Cards</title>
<link href="https://fonts.googleapis.com/css2?family=Lato:wght@400;700;900&display=swap" rel="stylesheet">
<style>
  :root{
    --stage:#2b2b2b;
    --stage-dark:#1a1a1a;
    --card-black:#050505;
    --card-white:#ffffff;
    --pattern-tone:#ececec;
    --teal:#2fb8b1;
    --ink:#1d1d1d;
    --white:#ffffff;
  }
  *{margin:0;padding:0;box-sizing:border-box;}
  html,body{width:1200px;height:875px;overflow:hidden;}
  body{
    background:linear-gradient(135deg,var(--stage) 0%,var(--stage-dark) 100%);
    font-family:"Lato",sans-serif;
    display:flex;align-items:center;justify-content:center;gap:50px;
  }
  .card{
    width:540px;height:309px;border-radius:18px;overflow:hidden;position:relative;
    box-shadow:0 18px 40px rgba(0,0,0,.45);
  }
  /* Front: logo side */
  .card--front{
    background:var(--card-black);
    display:flex;flex-direction:column;align-items:center;justify-content:center;gap:22px;
  }
  .brand-name{
    color:var(--white);font-weight:900;text-transform:uppercase;
    font-size:34px;letter-spacing:.06em;text-align:center;line-height:1.15;
  }
  .brand-services{
    color:var(--white);font-weight:400;font-size:14px;letter-spacing:.02em;
  }
  /* Back: contact side */
  .card--back{
    background:var(--card-white);
    display:flex;flex-direction:column;
  }
  .pattern-band{background:var(--pattern-tone);flex:none;}
  .pattern-band--top{height:66px;border-bottom:3px solid var(--ink);}
  .pattern-band--bottom{height:40px;border-top:2px solid var(--teal);}
  .contact{
    flex:1;
    display:flex;flex-direction:column;align-items:center;justify-content:center;
    padding:8px 0 12px;
  }
  .owner-name{
    color:var(--teal);font-weight:900;font-size:52px;letter-spacing:.03em;
    text-transform:uppercase;line-height:1;
  }
  .phone{
    color:var(--ink);font-weight:700;font-size:30px;letter-spacing:.32em;line-height:1.1;
    margin-top:10px;margin-right:-.32em;
  }
  .location{
    align-self:stretch;margin-top:16px;
    display:flex;align-items:center;gap:10px;
  }
  .location::before,.location::after{
    content:"";flex:1;height:2px;background:var(--teal);
  }
  .location-text{
    color:var(--ink);font-size:15px;font-weight:400;line-height:1;
    text-transform:uppercase;letter-spacing:.04em;
  }
</style>
</head>
<body>
  <section class="card card--front">
    <h1 class="brand-name">Birchline<br>Septic Solutions</h1>
    <p class="brand-services">Pumping, Inspections, Installs &amp; Repairs</p>
  </section>

  <section class="card card--back">
    <div class="pattern-band pattern-band--top" role="img" aria-label="Faint line-drawn pattern of septic pipes and fittings"></div>
    <div class="contact">
      <h2 class="owner-name">Colin Vandro</h2>
      <p class="phone">555-241-0387</p>
      <p class="location"><span class="location-text">Maplebrook, OH</span></p>
    </div>
    <div class="pattern-band pattern-band--bottom" role="img" aria-label="Faint line-drawn pattern of septic pipes and fittings"></div>
  </section>
</body>
</html>
```